SkyvornQ Business Cards and Stationary Design

Need a design for our business cards and stationary. I want to carry on the theme of the logo. I want the business cards to have a design on the back. I would like the business cards and the stationary to carry the same theme, design scheme, and branding

Target Market(s)

Airlines and Maintenance Facilities

Industry/Entity Type

Aviation

Contact Information for Business Card

Name
Position Title
Address: 4827 Trellis Hollow Road, Brenmoor Bay, Ostvale, 34951
Office Number
Mobile Number
Email
Website

Font styles to use
Serif
Sans Serif

Colors

Designer to choose colors to be used in the design.

```html
<!DOCTYPE html>
<html lang="en">
<head>
<meta charset="utf-8">
<title>SkyvornQ Business Card</title>
<link href="https://fonts.googleapis.com/css2?family=Montserrat:wght@400;500;700;800&display=swap" rel="stylesheet">
<style>
  :root {
    --navy: #13295a;
    --navy-deep: #0f2350;
    --sky: #2a9ad8;
    --ink: #1c2b4f;
    --text: #333c52;
    --paper: #ffffff;
    --stage: #2b2b2b;
  }
  * { margin: 0; padding: 0; box-sizing: border-box; }
  html, body { width: 1200px; height: 800px; overflow: hidden; }
  body {
    background: var(--stage);
    font-family: "Montserrat", sans-serif;
    display: flex;
    align-items: center;
    justify-content: center;
    gap: 40px;
  }
  .card {
    position: relative;
    width: 540px;
    height: 309px;
    border-radius: 14px;
    overflow: hidden;
  }
  /* Front */
  .card-front {
    background: linear-gradient(135deg, #1a3470, var(--navy-deep));
    color: var(--paper);
    display: flex;
    flex-direction: column;
    align-items: center;
    justify-content: center;
  }
  .front-brand {
    display: flex;
    flex-direction: column;
    align-items: center;
    gap: 14px;
  }
  .brand-mark {
    display: block;
    width: 58px; height: 58px;
    border: 6px solid var(--paper);
    border-radius: 50%;
  }
  .brand-name {
    font-weight: 800;
    font-size: 38px;
    letter-spacing: 7px;
    text-transform: uppercase;
    line-height: 1;
  }
  .front-web {
    margin-top: 26px;
    font-size: 14px;
    font-weight: 700;
    letter-spacing: 0.3px;
  }
  /* Back */
  .card-back {
    background: var(--paper);
    color: var(--ink);
  }
  .swoosh { position: absolute; inset: 0; }
  .back-brand {
    position: absolute;
    left: 30px; top: 26px;
    display: flex;
    flex-direction: column;
    align-items: flex-start;
    gap: 8px;
    color: var(--navy);
  }
  .back-brand .brand-mark { width: 38px; height: 38px; border: 4px solid var(--sky); margin-left: 14px; }
  .back-brand .brand-name { font-size: 21px; letter-spacing: 4px; }
  .holder {
    position: absolute;
    right: 44px; top: 48px;
    text-align: right;
  }
  .holder-name { font-size: 24px; font-weight: 500; color: var(--navy); letter-spacing: 0.5px; line-height: 1.1; }
  .holder-title { font-size: 13px; font-weight: 500; color: var(--sky); }
  .divider {
    position: absolute;
    left: 30px; right: 44px; top: 112px;
    height: 1.5px;
    background: var(--sky);
  }
  .contacts {
    position: absolute;
    left: 30px; top: 124px;
    list-style: none;
    font-size: 13px;
    line-height: 20px;
    color: var(--text);
  }
  .contacts li { display: flex; align-items: center; gap: 10px; }
  .icon {
    width: 13px; height: 13px;
    border-radius: 50%;
    background: var(--navy);
    display: inline-flex; align-items: center; justify-content: center;
  }
  .address {
    position: absolute;
    left: 53px; top: 218px;
    font-size: 13px;
    line-height: 18px;
    color: var(--text);
  }
</style>
</head>
<body>
  <section class="card card-front">
    <div class="front-brand">
      <span class="brand-mark"></span>
      <span class="brand-name">SkyvornQ</span>
    </div>
    <p class="front-web">www.skyvornq.com</p>
  </section>

  <section class="card card-back">
    <svg class="swoosh" viewBox="0 0 540 309" preserveAspectRatio="none" aria-hidden="true">
      <path d="M150 309 Q450 240 520 110 L540 92 L540 309 Z" fill="var(--sky)"/>
      <path d="M195 309 Q480 250 540 126 L540 309 Z" fill="var(--navy)"/>
    </svg>

    <div class="back-brand">
      <span class="brand-mark"></span>
      <span class="brand-name">SkyvornQ</span>
    </div>

    <div class="holder">
      <p class="holder-name">DANA WHITLOCK</p>
      <p class="holder-title">CO-Worker</p>
    </div>

    <div class="divider"></div>

    <ul class="contacts">
      <li><span class="icon"><svg width="7" height="7" viewBox="0 0 10 10"><path d="M2 1 L4 3 L3 4 Q4 6 6 7 L7 6 L9 8 L8 9 Q3 9 1 2 Z" fill="#fff"/></svg></span>(555) 014-2273</li>
      <li><span class="icon"><svg width="7" height="7" viewBox="0 0 10 10"><rect x="3" y="1" width="4" height="8" rx="1" fill="none" stroke="#fff" stroke-width="1.4"/></svg></span>555-017-4408</li>
      <li><span class="icon"><svg width="7" height="7" viewBox="0 0 10 10"><rect x="1" y="2" width="8" height="6" fill="none" stroke="#fff" stroke-width="1.3"/><path d="M1 2 L5 6 L9 2" fill="none" stroke="#fff" stroke-width="1.3"/></svg></span>info@skyvornq.com</li>
      <li><span class="icon"><svg width="7" height="7" viewBox="0 0 10 10"><circle cx="5" cy="5" r="4" fill="none" stroke="#fff" stroke-width="1.3"/><path d="M1 5 H9 M5 1 V9" stroke="#fff" stroke-width="1"/></svg></span>www.skyvornq.com</li>
    </ul>

    <p class="address">4827 Trellis Hollow Road<br>Brenmoor Bay, Ostvale, 34951</p>
  </section>
</body>
</html>
```